Velmo Swinger site - new website, blogsite and merchandise point, connection to tradeva

We are a well established Swingers Club in the North east of UK and already have an existing site. www.velmo-example.co.uk, BUT we have changed our logo and our information on the site needs to be updated.

We are changing our hosting site to Nimbrashost.example ,also wanting to start a blog which is linked to the club, plus we wish to sell a small exclusive range of Velmo linked merchandise which will also be available on Tradeva.

I have attached a pdf of the majority of the content. additionally we will provide pictures and a videoclip which should be able to be viewed by pc's, lap tops and mobile phones (the whole website must be fully accessible via phone).

The new site must be able to be updated by someone with medium computer knowledge (usually me), by no means expert. Updates will generally be new pictures and written information. The site must be able to be transferred to NimbrasHost.

Velmo is one of the countries leading clubs and emphasises friendliness, fun & safety for its members, we look after you to ensure your experience is the best we can offer. We are very proud of our reputation, built up over more than 10 years.

Target Market(s)

Swingers, dreamers & fantasists, alternative lifestyle people

Coding

Coded - Design and coding required

Number of Pages Required

5+ page

Font styles to use
Sans Serif

Colors
000000
ec1f27
fbfbfb
eeeeee
eaeaea

Requirements
Must have
• website with blog attached, link to tradeva & quidlo, ability to run videoclip and picture album and must be compatable to transfer easily to Nimbrashost and be updated by non-professional (who can learn)
• Straightforward & easy to navigate
• over 18 content page with enter button
Nice to have
• sexy site
• link to chirpster maybe
• black site would be nice with red or white writing
Should not have
• children and animals in anyway shape or form

```html
<!DOCTYPE html>
<html lang="en">
<head>
<meta charset="utf-8">
<title>Velmo – Swingers Club</title>
<link href="https://fonts.googleapis.com/css2?family=Cinzel:wght@400;700&family=Open+Sans:wght@400;600;700&display=swap" rel="stylesheet">
<style>
:root{
  --black:#000000;
  --red:#ec1f27;
  --white:#fbfbfb;
  --light:#eeeeee;
  --pale:#eaeaea;
  --ink:#111111;
  --dark-wine:#2a1012;
  --mid-grey:#2b2b2b;
  --head:'Cinzel', serif;
  --body:'Open Sans', sans-serif;
}
*{margin:0;padding:0;box-sizing:border-box}
html,body{width:1200px;height:3152px;overflow:hidden;background:var(--black)}
body{position:relative;font-family:var(--body);color:var(--white)}
.abs{position:absolute}
section,header,footer{position:absolute;left:0;width:1200px;overflow:hidden}

/* header / hero */
.hero{top:0;height:532px;background:linear-gradient(180deg,#1c2433 0%,#2f3644 45%,#3a2f26 75%,#1a1611 100%)}
.hero-photo{position:absolute;inset:0;background:radial-gradient(ellipse at 58% 62%,rgba(214,170,110,.45),transparent 55%),linear-gradient(180deg,rgba(0,0,0,.35),rgba(0,0,0,.25))}
.logo{left:99px;top:26px;font-family:var(--head);font-size:42px;letter-spacing:2px;color:var(--white)}
.topbar{right:99px;top:14px;font-size:15px;display:flex;gap:24px;align-items:center}
.topbar span{display:flex;align-items:center;gap:8px}
.topbar svg{fill:var(--red)}
.main-nav{left:323px;top:54px;display:flex;gap:18px;font-size:15px;align-items:center}
.main-nav a{color:var(--white);text-decoration:none}
.main-nav a.active{color:var(--red)}
.hero-title{left:0;width:1200px;top:160px;text-align:center;font-family:var(--head);font-size:76px;letter-spacing:18px;color:var(--white)}
.hero-lead{left:200px;width:800px;top:262px;text-align:center;font-size:22px;font-weight:600;line-height:34px}
.btn-outline{left:513px;top:353px;width:113px;height:46px;border:2px solid var(--white);color:var(--white);font-size:13px;font-weight:700;display:flex;align-items:center;justify-content:center;border-radius:3px;text-transform:uppercase}
.dots{left:0;width:1200px;top:472px;display:flex;justify-content:center;gap:7px}
.dots i{width:12px;height:12px;border:2px solid var(--white);border-radius:50%}
.dots i.on{background:var(--white)}

/* welcome */
.welcome{top:532px;height:519px;background:linear-gradient(180deg,#e3232b,#d51f27)}
.welcome-photo{position:absolute;inset:0;background:radial-gradient(ellipse at 80% 30%,rgba(120,10,15,.35),transparent 60%),radial-gradient(ellipse at 25% 80%,rgba(255,120,120,.18),transparent 55%)}
.welcome-frame{left:32px;top:33px;width:1136px;height:448px;border:2px solid rgba(251,251,251,.75)}
.section-title{font-family:var(--head);font-size:40px;text-align:center;width:1200px;left:0;color:var(--white)}
.welcome .section-title{top:72px}
.welcome-text{left:200px;width:800px;top:150px;text-align:center;font-size:12.5px;line-height:28px}
.feature{width:300px;text-align:center}
.feature .ring{width:152px;height:152px;border:3px solid var(--white);border-radius:50%;margin:0 auto;display:flex;align-items:center;justify-content:center}
.feature .ring svg{fill:var(--white)}
.feature p{margin-top:30px;font-family:var(--head);font-size:19px;text-transform:uppercase}

/* about */
.about{top:1051px;height:510px;background:linear-gradient(90deg,#1a0a0b,#2c1416 60%,#1a0c0c)}
.about-photo{left:99px;top:65px;width:403px;height:384px;border:3px solid var(--light);background:linear-gradient(135deg,#5a0f1e,#a3263f 45%,#2a0a10)}
.about-title{left:559px;top:80px;font-family:var(--head);font-size:36px;line-height:48px}
.about-text{left:559px;top:180px;width:540px;font-size:13px;line-height:27px}
.about-text p+p{margin-top:24px}
.btn-ghost{width:128px;height:37px;border:2px solid var(--light);color:var(--red);font-size:12px;font-weight:700;display:flex;align-items:center;justify-content:center;border-radius:3px;text-transform:uppercase}
.about .btn-ghost{left:559px;top:412px}

/* membership */
.membership{top:1561px;height:383px;background:linear-gradient(180deg,#333,#242424)}
.card{top:89px;width:484px;height:214px;border:3px solid var(--pale);background:var(--ink);display:flex}
.card-photo{width:216px;height:100%;flex:none}
.card-body{padding:18px 18px 0 20px}
.card-body h3{font-family:var(--head);font-weight:400;color:var(--red);font-size:20px}
.card-body p{font-size:13px;line-height:24px;margin-top:14px}
.btn-red{display:inline-flex;align-items:center;justify-content:center;width:134px;height:44px;background:var(--red);color:var(--white);font-size:12px;font-weight:700;border-radius:3px;margin-top:14px;text-transform:uppercase}

/* blog */
.blog{top:1944px;height:406px;background:linear-gradient(180deg,#3a1516,#1d0a0b)}
.blog .section-title{top:64px}
.post{top:158px;width:470px;height:170px}
.post-photo{position:absolute;left:0;top:0;width:189px;height:170px;border:3px solid var(--light)}
.post-body{position:absolute;left:214px;top:0;width:260px}
.post-body h3{font-family:var(--head);font-weight:400;font-size:17px;line-height:25px}
.post-meta{font-size:12px;margin:10px 0;display:flex;gap:16px;align-items:center}
.post-meta svg{fill:var(--white);margin-right:6px;vertical-align:-2px}
.post-body p{font-size:12px;line-height:21px}
.post-body a{display:block;margin-top:12px;color:var(--red);font-size:12px;font-weight:700;text-decoration:none}

/* products */
.products{top:2350px;height:534px;background:linear-gradient(180deg,#262626,#3a3a3a 60%,#1c1c1c)}
.products .section-title{top:66px}
.product{top:145px;width:238px}
.product-photo{width:238px;height:216px;background:linear-gradient(180deg,#ffffff,var(--light))}
.product p{font-size:14.5px;line-height:25px;margin-top:12px}
.product-foot{display:flex;justify-content:space-between;align-items:center;margin-top:10px}
.price{color:var(--red);font-weight:700;font-size:16px}
.shop{font-size:15px;font-weight:600;color:var(--white)}
.arrow{top:236px;width:36px;height:36px;border:2px solid var(--white);border-radius:50%;display:flex;align-items:center;justify-content:center}
.arrow svg{stroke:var(--white);fill:none;stroke-width:2}

/* footer */
.site-footer{top:2884px;height:268px;background:var(--black);border-top:5px solid var(--red)}
.contact{top:56px;display:flex;align-items:center;gap:20px;font-size:14.5px;font-weight:600;line-height:22px}
.contact .ring{width:44px;height:44px;border:2px solid var(--white);border-radius:50%;display:flex;align-items:center;justify-content:center;flex:none}
.contact svg{fill:var(--white)}
.footer-nav{left:0;width:1200px;top:138px;display:flex;justify-content:center;gap:24px;font-size:15px;font-weight:600;text-transform:uppercase;padding-right:80px}
.footer-rule{left:99px;top:183px;width:1002px;height:1px;background:#333}
.copyright{left:99px;top:216px;font-size:12px}
.social{top:203px;width:36px;height:36px;border:2px solid var(--white);border-radius:50%}
</style>
</head>
<body>

<header class="hero">
  <div class="hero-photo" role="img" aria-label="Night view over the city with the lit cathedral on the hill"></div>
  <div class="abs logo">Velmo</div>
  <div class="abs topbar">
    <span><svg width="14" height="14" viewBox="0 0 24 24"><path d="M6.6 10.8a15.1 15.1 0 006.6 6.6l2.2-2.2a1 1 0 011-.25 11.4 11.4 0 003.6.57 1 1 0 011 1V20a1 1 0 01-1 1A17 17 0 013 4a1 1 0 011-1h3.5a1 1 0 011 1c0 1.25.2 2.45.57 3.57a1 1 0 01-.25 1z"/></svg>0700 5550142</span>
    <span><svg width="16" height="13" viewBox="0 0 24 18"><path d="M0 0h24v2L12 10 0 2zM0 4.5l12 8 12-8V18H0z"/></svg>velmoswingers@mailbox.example</span>
  </div>
  <nav class="abs main-nav">
    <a class="active">Home</a><a>Diary</a><a>Theme Parties</a><a>TV/TG and Admirers</a><a>Membership</a><a>FAQs</a><a>Rooms</a><a>Contact Us</a><a>Links</a>
    <svg width="16" height="16" viewBox="0 0 24 24" fill="none" stroke="#fbfbfb" stroke-width="3"><circle cx="10" cy="10" r="7"/><path d="M15 15l7 7"/></svg>
  </nav>
  <h1 class="abs hero-title">VELMO</h1>
  <p class="abs hero-lead">We are a Swingers Club in the UK Velmo is one of the countries leading clubs and emphasises friendliness, fun &amp; safety for its members.</p>
  <div class="abs btn-outline">Get More Info</div>
  <div class="abs dots"><i class="on"></i><i></i><i></i><i></i></div>
</header>

<section class="welcome">
  <div class="welcome-photo" role="img" aria-label="Red-tinted photo of a club bedroom"></div>
  <div class="abs welcome-frame"></div>
  <h2 class="abs section-title">Welcome to Velmo</h2>
  <p class="abs welcome-text">We are the best in the North East, and have recently been voted No 2 club in the UK. We have retained the coveted title of No 1 friendliest club in the UK (in joint 1st place with our great friends "The Pleasure Lounge", London).</p>
  <div class="abs feature" style="left:73px;top:237px">
    <div class="ring"><svg width="60" height="66" viewBox="0 0 60 66"><path d="M4 4h52L34 30v26h12v6H14v-6h12V30z"/></svg></div>
    <p>Leading Clubs</p>
  </div>
  <div class="abs feature" style="left:449px;top:237px">
    <div class="ring"><svg width="72" height="56" viewBox="0 0 72 56"><circle cx="36" cy="12" r="10"/><path d="M20 56v-18a16 16 0 0132 0v18z"/><circle cx="13" cy="18" r="8"/><path d="M0 54V40a13 13 0 0118-12v26z"/><circle cx="59" cy="18" r="8"/><path d="M72 54V40a13 13 0 00-18-12v26z"/></svg></div>
    <p>Emphasises Friendliness</p>
  </div>
  <div class="abs feature" style="left:825px;top:237px">
    <div class="ring"><svg width="60" height="68" viewBox="0 0 60 68"><path d="M30 0l28 10v20c0 18-12 32-28 38C14 62 2 48 2 30V10z"/><path d="M17 34l9 9 17-18" stroke="#e3232b" stroke-width="6" fill="none"/></svg></div>
    <p>Fun &amp; Safety</p>
  </div>
</section>

<section class="about">
  <div class="abs about-photo" role="img" aria-label="Red-lit play room with a cross frame and a large bed"></div>
  <h2 class="abs about-title">Velmo :: A Great<br>Place To Meet And Play!</h2>
  <div class="abs about-text">
    <p>We are the best Swingers Club in the North East, and also voted No 2 club in the UK.</p>
    <p>We have retained the coveted title of No 1 friendliest club in the UK (in joint 1st place with our great friends "The Pleasure Lounge", London). This prestigious award has been given to us by a panel of "mystery voters" (swingers, singles &amp; couples) working with the publication called "Nights in the Cities" a copy of which is available in reception. Please see our Frequently Asked Questions and Membership pages for more information about the club and its facilities. Velmo was established in Sunderland in 2004 by Marcus.</p>
  </div>
  <div class="abs btn-ghost">Read More</div>
</section>

<section class="membership">
  <div class="abs card" style="left:99px">
    <div class="card-photo" role="img" aria-label="Bedroom with red canopy and animal-print bedding" style="background:linear-gradient(135deg,#7a1a1e,#c7443e 50%,#3a2a24)"></div>
    <div class="card-body">
      <h3>Membership Fees</h3>
      <p>New members (Couples and Single guys) - (annual) £30, this now includes the next 2 visits half price.</p>
      <span class="btn-red">Read More</span>
    </div>
  </div>
  <div class="abs card" style="left:618px">
    <div class="card-photo" role="img" aria-label="Warm-lit bedroom with red walls and twin beds" style="background:linear-gradient(135deg,#3a1a10,#c5542a 55%,#5a2414)"></div>
    <div class="card-body">
      <h3>Membership Discounts</h3>
      <p>We discount entry and membership to support Her Majesty's Forces (serving and retired)..</p>
      <span class="btn-red">Read More</span>
    </div>
  </div>
</section>

<section class="blog">
  <h2 class="abs section-title">Our Blog</h2>
  <article class="abs post" style="left:99px">
    <div class="post-photo" role="img" aria-label="Lounge room with a wall screen" style="background:linear-gradient(135deg,#2a2420,#8a6a4a 60%,#3a2a20)"></div>
    <div class="post-body">
      <h3>AT VERO EOS ET ACCUSAMUS ET IUSTO ODIO DIGNIPRA</h3>
      <div class="post-meta"><span><svg width="12" height="12" viewBox="0 0 12 12"><path d="M0 2h12v10H0zM2 0h2v3H2zM8 0h2v3H8z"/></svg>17/06/2017</span><span><svg width="11" height="12" viewBox="0 0 11 12"><circle cx="5.5" cy="3" r="3"/><path d="M0 12a5.5 5.5 0 0111 0z"/></svg>Marcus</span></div>
      <p>Nam libero tempore, cum soluta nobis elindi optio cumque nihil impedo</p>
      <a>READ MORE &gt;&gt;</a>
    </div>
  </article>
  <article class="abs post" style="left:628px">
    <div class="post-photo" role="img" aria-label="Bedroom with dark headboard and white bedding" style="background:linear-gradient(135deg,#3a3440,#9a8a84 55%,#2a2226)"></div>
    <div class="post-body">
      <h3>AT VERO EOS ET ACCUSAMUS ET IUSTO ODIO DIGNIPRA</h3>
      <div class="post-meta"><span><svg width="12" height="12" viewBox="0 0 12 12"><path d="M0 2h12v10H0zM2 0h2v3H2zM8 0h2v3H8z"/></svg>17/06/2017</span><span><svg width="11" height="12" viewBox="0 0 11 12"><circle cx="5.5" cy="3" r="3"/><path d="M0 12a5.5 5.5 0 0111 0z"/></svg>Marcus</span></div>
      <p>Nam libero tempore, cum soluta nobis elindi optio cumque nihil impedo</p>
      <a>READ MORE &gt;&gt;</a>
    </div>
  </article>
</section>

<section class="products">
  <h2 class="abs section-title">Velmo Products</h2>
  <div class="abs arrow" style="left:39px"><svg width="12" height="14" viewBox="0 0 12 14"><path d="M8 2L3 7l5 5"/></svg></div>
  <div class="abs arrow" style="left:1123px"><svg width="12" height="14" viewBox="0 0 12 14"><path d="M4 2l5 5-5 5"/></svg></div>

  <div class="abs product" style="left:99px">
    <div class="product-photo" role="img" aria-label="Black branded t-shirt"></div>
    <p>At vero eos et accusamus eiuto odio dignissimos duc.</p>
    <div class="product-foot"><span class="price">$20.00</span><span class="shop">tradeva</span></div>
  </div>
  <div class="abs product" style="left:353px">
    <div class="product-photo" role="img" aria-label="Red branded mug"></div>
    <p>At vero eos et accusamus eiuto odio dignissimos duc.</p>
    <div class="product-foot"><span class="price">$20.00</span><span class="shop">tradeva</span></div>
  </div>
  <div class="abs product" style="left:609px">
    <div class="product-photo" role="img" aria-label="Branded wine bottle"></div>
    <p>At vero eos et accusamus eiuto odio dignissimos duc.</p>
    <div class="product-foot"><span class="price">$20.00</span><span class="shop">tradeva</span></div>
  </div>
  <div class="abs product" style="left:864px">
    <div class="product-photo" role="img" aria-label="Red branded cap"></div>
    <p>At vero eos et accusamus eiuto odio dignissimos duc.</p>
    <div class="product-foot"><span class="price">$20.00</span><span class="shop">tradeva</span></div>
  </div>
</section>

<footer class="site-footer">
  <div class="abs contact" style="left:184px">
    <span class="ring"><svg width="14" height="20" viewBox="0 0 14 20"><path d="M7 0a7 7 0 017 7c0 5-7 13-7 13S0 12 0 7a7 7 0 017-7zm0 4a3 3 0 100 6 3 3 0 000-6z"/></svg></span>
    <span>88 Wessel Street, 4th Floor<br>London</span>
  </div>
  <div class="abs contact" style="left:499px">
    <span class="ring"><svg width="18" height="18" viewBox="0 0 24 24"><path d="M6.6 10.8a15.1 15.1 0 006.6 6.6l2.2-2.2a1 1 0 011-.25 11.4 11.4 0 003.6.57 1 1 0 011 1V20a1 1 0 01-1 1A17 17 0 013 4a1 1 0 011-1h3.5a1 1 0 011 1c0 1.25.2 2.45.57 3.57a1 1 0 01-.25 1z"/></svg></span>
    <span>0700 5550142</span>
  </div>
  <div class="abs contact" style="left:722px">
    <span class="ring"><svg width="18" height="14" viewBox="0 0 24 18"><path d="M0 0h24v2L12 10 0 2zM0 4.5l12 8 12-8V18H0z"/></svg></span>
    <span>velmoswingers@mailbox.example</span>
  </div>
  <nav class="abs footer-nav">
    <span>Home</span><span>Diary</span><span>Theme Parties</span><span>TV/TG and Admirers</span><span>Membership</span><span>FAQs</span><span>Rooms</span><span>Contact Us</span><span>Links</span>
  </nav>
  <div class="abs footer-rule"></div>
  <p class="abs copyright">Copyrights © 2017, Velmo. All rights reserved.</p>
  <span class="abs social" style="left:978px" role="img" aria-label="Social network link"></span>
  <span class="abs social" style="left:1026px" role="img" aria-label="Chirpster link"></span>
  <span class="abs social" style="left:1075px" role="img" aria-label="Social network link"></span>
</footer>

</body>
</html>
```